Spiritual Healing bussiness needs logo/business card

Simple, clean looking logo/card
For spiritual business with healing services and occult rituals

Contact Information for Business Card

Needs my name: Tobin Varley
Business name: Lantern Healing Shop
Services provided and worded in this way:

Reiki Healing
Tarot
Oils
Rituals Of Change

Can look occult like but with light energy.

Colors
0255a3
3276b5
85abd2
33a6d7
85cae6
0292cd

```html
<!DOCTYPE html>
<html lang="en">
<head>
<meta charset="UTF-8">
<title>Lantern Healing Shop – Business Card</title>
<link href="https://fonts.googleapis.com/css2?family=Lato:wght@400;700&family=Arvo:wght@400;700&display=swap" rel="stylesheet">
<style>
  :root {
    --backdrop: #1c1c1e;
    --card: #101011;
    --rule: #3a3a3e;
    --silver: #d4d4d6;
    --text-light: #e6e6e8;
    --blue-deep: #0255a3;
    --blue-mid: #3276b5;
    --blue-bright: #0292cd;
    --blue-sky: #33a6d7;
  }
  * { margin: 0; padding: 0; box-sizing: border-box; }
  html, body { width: 1200px; height: 900px; overflow: hidden; }
  body {
    background: var(--backdrop);
    font-family: "Lato", Arial, sans-serif;
    position: relative;
  }
  .card {
    position: absolute;
    left: 320px;
    width: 560px;
    height: 320px;
    background: var(--card);
    border-radius: 22px;
    box-shadow: 0 18px 40px rgba(0,0,0,0.55);
    overflow: hidden;
  }
  .card--back { top: 80px; }
  .card--front { top: 500px; }

  /* back side */
  .back-mark {
    position: absolute;
    top: 46px; left: 0; width: 100%;
    display: flex; flex-direction: column; align-items: center; gap: 14px;
  }
  .back-mark__circle {
    width: 96px; height: 96px; border-radius: 50%;
    border: 9px solid var(--silver);
  }
  .back-mark__name {
    font-family: "Arvo", Georgia, serif;
    font-size: 20px; color: var(--silver);
  }
  .back-rule {
    position: absolute; left: 40px; right: 40px; top: 238px;
    height: 1px; background: var(--rule);
  }
  .services {
    position: absolute; right: 40px; top: 252px;
    display: flex; gap: 12px; list-style: none;
    font-size: 15px; color: var(--text-light);
  }
  .services li + li::before {
    content: ""; display: inline-block;
    width: 6px; height: 6px; border-radius: 50%;
    background: var(--text-light);
    margin-right: 10px; vertical-align: middle;
  }

  /* front side */
  .brand {
    position: absolute; right: 40px; top: 30px;
    display: flex; flex-direction: column; align-items: flex-end; gap: 12px;
  }
  .brand__circle {
    width: 92px; height: 92px; border-radius: 50%;
    border: 9px solid var(--blue-deep);
    margin-right: 90px;
  }
  .brand__name {
    font-family: "Arvo", Georgia, serif;
    font-size: 26px; color: var(--blue-deep);
  }
  .front-rule {
    position: absolute; left: 40px; right: 40px; top: 190px;
    height: 1px; background: var(--rule);
  }
  .website {
    position: absolute; right: 40px; top: 202px;
    font-size: 16px; color: var(--blue-bright);
  }
  .person {
    position: absolute; left: 40px; bottom: 30px;
  }
  .person__name {
    font-family: "Arvo", Georgia, serif;
    font-size: 24px; color: var(--blue-mid);
    margin-bottom: 8px;
  }
  .contact { list-style: none; font-size: 17px; color: var(--text-light); }
  .contact li { display: flex; align-items: center; gap: 8px; margin-top: 4px; }
  .contact svg { width: 20px; height: 20px; flex: none; }
</style>
</head>
<body>
  <section class="card card--back" aria-label="Card back">
    <div class="back-mark">
      <div class="back-mark__circle"></div>
      <div class="back-mark__name">Lantern Healing Shop</div>
    </div>
    <div class="back-rule"></div>
    <ul class="services">
      <li>Reiki Healing</li>
      <li>Tarot</li>
      <li>Oils</li>
      <li>Rituals Of Change</li>
    </ul>
  </section>

  <section class="card card--front" aria-label="Card front">
    <div class="brand">
      <div class="brand__circle"></div>
      <div class="brand__name">Lantern Healing Shop</div>
    </div>
    <div class="front-rule"></div>
    <div class="website">www.LanternHealingShop.com</div>
    <div class="person">
      <div class="person__name">Tobin Varley</div>
      <ul class="contact">
        <li>
          <svg viewBox="0 0 20 20" aria-hidden="true">
            <circle cx="10" cy="10" r="9" fill="none" stroke="#0255a3" stroke-width="1.6"/>
            <path d="M6 8.5c0-1.2 1.8-2 4-2s4 .8 4 2l-1.4.6-.6-1.2h-4l-.6 1.2z M7 10h6l1 3.5H6z" fill="#0255a3"/>
          </svg>
          044-555 010 222
        </li>
        <li>
          <svg viewBox="0 0 20 20" aria-hidden="true">
            <circle cx="10" cy="10" r="9" fill="none" stroke="#0255a3" stroke-width="1.6"/>
            <rect x="5.5" y="7" width="9" height="6.5" fill="#0255a3"/>
            <path d="M5.5 7l4.5 3.5L14.5 7" fill="none" stroke="#101011" stroke-width="1"/>
          </svg>
          hello@lanternhealing.com
        </li>
      </ul>
    </div>
  </section>
</body>
</html>
```